New Business Card for Odd Fern Designs

I create and make jewellery and Clothing. But when it comes to business card design I fail completely.

Sketching is my area, drawing, putting things together neatly, not so much.

Here is a little blurb about my company:

Odd Fern Designs is a truly unique customer experience. Work one on one with Owner Petra Wolcott to make your costuming dreams come true.

Not after a costume? Browse through the store for a look at beautiful and unique piece of jewellery. Each piece has been put together by Petra, by hand. You'll find Steampunk, gothic, lolita and other quirky styles.

Want something else? What abotu a pair of warm kitty paws? A Pair of Kitty ears? A pony tail to wear on your jeans? There are so many options and things to choose! You will want to take it all home.

I have attached the previous business card with my mascot "Greta" As you can see there is a very Greta in Cloudmere feel to the overall company, with references to The Tin Tinker, and the idea that "We are all made here".

Colour's to use would be purple and blue. The winning design would show the unique but professional approach that Odd Fern Designs takes when creating each piece for their customers.

Reason: Wanted to give you a chance to go over feed back that has been sent out. I am committed to paying for the design that I will use. I think another week will help tweak things up.

Target Market(s)

Nerds, Geeks and Sci-Fi people aged 20 - 34 both Male and Female

Industry/Entity Type

Store

Requirements
Must have
• Website address: www.oddferndesigns.example

Yeah, rest is up too you!
Nice to have
• Honestly, if you could make the whole thing look like a Edwin Marlowe "Greta in Cloudmere" Drawing with the same line working style that would be amazing!

But I won't restrict you! I'd like to see what you can come up with.

```html
<!DOCTYPE html>
<html lang="en">
<head>
<meta charset="utf-8">
<title>Odd Fern Designs — Business Card</title>
<link rel="stylesheet" href="https://fonts.googleapis.com/css2?family=Courgette&display=swap">
<style>
  :root {
    --card-purple: #8a5289;
    --pattern-teal: #1aa8a8;
    --pattern-white: #ffffff;
    --web-blue: #16a6c9;
  }
  html, body {
    margin: 0;
    padding: 0;
    width: 1200px;
    height: 697px;
    overflow: hidden;
    background: var(--card-purple);
  }
  .card {
    position: relative;
    width: 1200px;
    height: 697px;
    background: var(--card-purple);
  }
  .zigzag-band {
    position: absolute;
    left: 0;
    top: 153px;
    width: 1200px;
    height: 352px;
    background:
      radial-gradient(ellipse 230px 190px at 470px 176px,
        rgba(255,255,255,0.55), rgba(255,255,255,0) 100%),
      linear-gradient(180deg,
        rgba(26,168,168,0.55) 0%,
        rgba(180,150,190,0.55) 30%,
        rgba(26,168,168,0.45) 55%,
        rgba(200,170,205,0.5) 80%,
        rgba(220,200,225,0.45) 100%);
  }
  .website {
    position: absolute;
    left: 0;
    right: 0;
    top: 530px;
    margin: 0;
    text-align: center;
    font-family: "Courgette", cursive;
    font-size: 58px;
    line-height: 1;
    color: var(--web-blue);
    letter-spacing: 0.5px;
  }
</style>
</head>
<body>
  <main class="card">
    <div class="zigzag-band" role="img" aria-label="Decorative band of dotted teal and white zigzag lines across the card"></div>
    <p class="website">www.oddferndesigns.example</p>
  </main>
</body>
</html>
```